Veltrano.co - Polar Expeditions Specialists

We need a modern, visually striking business card for Veltrano.co, a company specialized in selling expedition cruises to the most remote regions on Earth, with a focus on the Arctic and Antarctica. The design should instantly communicate that the cardholder is an expert in polar travel. Use clean, premium aesthetics with cool tones like icy blue and white, possibly incorporating polar imagery (ice, glaciers, penguins, etc.)

Attached the logo

Contact Information for Business Card

Feels high-end and trustworthy.. Visually memorable — encourages people to keep it

Colors
0054AA
0677BA
7BADD7
CADEEF
E8F1F8

Requirements
Must have
• ice, glaciers, penguins, montains
Nice to have
• modern, transparente,

```html
<!DOCTYPE html>
<html lang="en">
<head>
<meta charset="UTF-8">
<title>Veltrano.co – Business Card</title>
<link href="https://fonts.googleapis.com/css2?family=Poppins:wght@400;500;700&display=swap" rel="stylesheet">
<style>
  :root {
    --bg: #2b2c30;
    --card-white: #fbfbfc;
    --navy: #12122a;
    --brand-blue: #2f6fb3;
    --text-light: #f2f4f8;
  }
  * { margin: 0; padding: 0; box-sizing: border-box; }
  html, body { width: 1200px; height: 900px; overflow: hidden; background: var(--bg); font-family: "Poppins", sans-serif; }
  .stage { position: relative; width: 1200px; height: 900px; }
  .card {
    position: absolute; width: 640px; height: 365px; border-radius: 26px; overflow: hidden;
    box-shadow: 0 14px 30px rgba(0,0,0,.45);
  }
  .card-front { left: 360px; top: 60px; background: var(--card-white); }
  .card-back { left: 200px; top: 475px; background: var(--navy); }

  .front-brand { position: absolute; inset: 0; display: flex; flex-direction: column; align-items: center; justify-content: center; }
  .brand-name { font-weight: 700; color: var(--brand-blue); line-height: 1; letter-spacing: -0.5px; }
  .front-brand .brand-name { font-size: 78px; }
  .brand-tagline { font-weight: 500; color: var(--brand-blue); }
  .front-brand .brand-tagline { font-size: 23px; margin-top: 14px; }

  .back-shape { position: absolute; inset: 0; }
  .back-brand { position: absolute; left: 310px; width: 330px; top: 130px; display: flex; flex-direction: column; align-items: center; }
  .back-brand .brand-name { font-size: 46px; }
  .back-brand .brand-tagline { font-size: 13.5px; margin-top: 8px; }

  .holder { position: absolute; left: 42px; top: 78px; color: var(--text-light); }
  .holder-accent { position: absolute; left: 0; top: 82px; width: 5px; height: 34px; background: var(--brand-blue); }
  .holder-name { font-size: 27px; font-weight: 700; color: var(--brand-blue); line-height: 1.1; }
  .holder-role { font-size: 15px; margin-top: 2px; }
  .holder-address { font-size: 15px; line-height: 1.35; margin-top: 16px; }
  .contact-list { list-style: none; margin-top: 14px; font-size: 15px; line-height: 1.4; }
  .contact-list li { display: flex; align-items: center; gap: 8px; }
  .contact-icon { width: 13px; height: 13px; fill: var(--brand-blue); flex: none; }
</style>
</head>
<body>
<main class="stage">
  <section class="card card-front" aria-label="Business card front">
    <div class="front-brand">
      <span class="brand-name">Veltrano.co</span>
      <span class="brand-tagline">Polar Expeditions Specialists</span>
    </div>
  </section>

  <section class="card card-back" aria-label="Business card back">
    <svg class="back-shape" width="640" height="365" viewBox="0 0 640 365">
      <path d="M345 0 C 240 70 225 270 305 365 L 640 365 L 640 0 Z" fill="var(--card-white)"/>
      <path d="M283 115 C 240 215 250 310 300 365 L 320 365 C 268 305 262 215 283 115 Z" fill="var(--brand-blue)"/>
    </svg>
    <div class="holder-accent"></div>
    <div class="holder">
      <p class="holder-name">Marcus Helden</p>
      <p class="holder-role">CEO &amp; Founder</p>
      <p class="holder-address">42 Harbor Point Avenue,<br>Lakeview, ME 04921 USA</p>
      <ul class="contact-list">
        <li><svg class="contact-icon" viewBox="0 0 24 24"><path d="M6.6 10.8a15 15 0 0 0 6.6 6.6l2.2-2.2c.3-.3.7-.4 1-.2 1.1.4 2.3.6 3.6.6.6 0 1 .4 1 1V20c0 .6-.4 1-1 1A17 17 0 0 1 3 4c0-.6.4-1 1-1h3.5c.6 0 1 .4 1 1 0 1.3.2 2.5.6 3.6.1.3 0 .7-.2 1z"/></svg>+1.555.014.782</li>
        <li><svg class="contact-icon" viewBox="0 0 24 24"><path d="M2 5h20v14H2z M2 5l10 8 10-8" fill="var(--brand-blue)"/></svg>hello@veltrano.co</li>
        <li><svg class="contact-icon" viewBox="0 0 24 24"><circle cx="12" cy="12" r="10"/></svg>www.veltrano.co</li>
      </ul>
    </div>
    <div class="back-brand">
      <span class="brand-name">Veltrano.co</span>
      <span class="brand-tagline">Polar Expeditions Specialists</span>
    </div>
  </section>
</main>
</body>
</html>
```